Marwick Law Letterhead

We need a new letterhead design for a Law Firm. The address for the law firm is 1475 Calloway Street, Suite 210, Houston, Texas 77041. Phone Number: 832-361-9027; Fax Number: 832-614-7359. The logo is uploaded to the project.

```html
<!DOCTYPE html>
<html lang="en">
<head>
<meta charset="utf-8">
<title>Marwick Law Letterhead</title>
<link href="https://fonts.googleapis.com/css2?family=Mulish:wght@400;500;700&display=swap" rel="stylesheet">
<style>
  :root {
    --backdrop: #e8e8e8;
    --paper: #ffffff;
    --navy: #1f2d5c;
    --crimson: #d3202a;
    --ink: #2b2b2b;
    --ink-dark: #111111;
    --signature: #1a1a1a;
  }
  * { margin: 0; padding: 0; box-sizing: border-box; }
  html, body {
    width: 1154px; height: 1200px; overflow: hidden;
    background: var(--backdrop);
    font-family: "Mulish", sans-serif;
  }
  .letterhead {
    position: absolute; left: 148px; top: 0;
    width: 858px; height: 1200px;
    background: var(--paper);
    box-shadow: -8px 10px 30px rgba(0,0,0,0.25);
  }
  .brand {
    position: absolute; left: 29px; top: 96px;
    display: flex; align-items: center; gap: 12px;
  }
  .brand-mark {
    width: 40px; height: 40px; background: var(--navy);
  }
  .brand-name {
    font-size: 32px; font-weight: 700; color: var(--navy);
    letter-spacing: 0.5px;
  }
  .date {
    position: absolute; right: 34px; top: 274px;
    font-size: 16px; color: var(--ink-dark);
  }
  .recipient {
    position: absolute; left: 32px; top: 287px;
    font-size: 15px; line-height: 21.3px; color: var(--ink-dark);
  }
  .body-copy {
    position: absolute; left: 34px; top: 372px; width: 794px;
    font-size: 14.6px; line-height: 21.3px; color: var(--ink);
    text-align: justify; hyphens: auto;
  }
  .body-copy p + p { margin-top: 21.3px; }
  .sign-off {
    position: absolute; left: 31px; top: 980px;
    font-size: 17px; color: var(--ink-dark);
  }
  .signature {
    position: absolute; left: 29px; top: 1010px;
    width: 97px; height: 28px;
    background: linear-gradient(90deg, rgba(26,26,26,0.15), rgba(26,26,26,0.05));
    border-radius: 4px;
  }
  .contact {
    position: absolute; left: 0; right: 0; top: 1126px;
    display: flex; justify-content: center; gap: 14px;
    font-size: 15px; color: var(--ink-dark);
  }
  .contact-item { display: flex; align-items: center; gap: 8px; }
  .contact-item svg { width: 14px; height: 14px; }
  .address {
    position: absolute; left: 0; right: 0; top: 1154px;
    text-align: center; font-size: 15px; color: var(--ink-dark);
  }
</style>
</head>
<body>
  <main class="letterhead">
    <div class="brand">
      <span class="brand-mark"></span>
      <span class="brand-name">Marwick Law</span>
    </div>

    <div class="date">DATE:05-Jan-2022</div>

    <div class="recipient">
      Mr/s<br>
      First Name and Last Name<br>
      Company Name<br>
      Address
    </div>

    <div class="body-copy">
      <p>Lorem ipsum dolor sit amet,consectetur adipiscing sed do eiusmod tempor incididunt laboreet dolore magna aliqua.Ut enim ad minim.veniam, quis nostrud exercitation ullamco laboris nisi ut aliquip exea commodo consequat.Lorem ipsum dolor sit amet,consectetur adipiscing sed do eiusmod tempor incididunt.labore et dolore magna aliqua. Ut enim</p>
      <p>Lorem ipsum dolor sit amet, consectetur adipiscing sed do eiusmod tempor incididunt labore et dolore magna aliqua. Ut enim ad minim veniam, quis nostrud exercitation ullamco laboris nisi ut aliquip exea commodo consequat.Duis aute irure dolor in reprehenderit in voluptate velit esse cillum irure dolor in reprehenderit in voluptate velit esse irure</p>
      <p>Lorem ipsum dolor sit amet, consectetur adipiscing sed do eiusmod tempor incididunt labore et dolore magna aliqua. consequat. Duis aute irure dolor in.reprehenderit in voluptate velit esse cillum dolore eu fugiat nulla pariatur. Excepteur sint occaecat cupidatat non proident, sunt in culpa qui officia deserunt mollit,</p>
      <p>Lorem ipsum dolor sit amet, consectetur adipiscing sed do eiusmod tempor incididunt labore et dolore magna aliqua. Ut enim Lorem ipsum dolor sit amet, consectetur adipiscing sed do eiusmod tempor incididunt labore et dolore magna aliqua. Ut enim Lorem ipsum aliqua.ipsum</p>
      <p>Lorem ipsum dolor sit amet, consectetur adipiscing sed do eiusmod tempor incididunt labore et dolore magna aliqua. Ut enim ad minim veniam, quis nostrud exercitation ullamco laboris nisi ut aliquip exea commodo consequat.Duis aute irure dolor in reprehenderit in voluptate velit esse cillum irure dolor in reprehenderit in voluptate velit esse irure</p>
      <p>Lorem ipsum dolor sit amet, consectetur adipiscing sed do eiusmod tempor incididunt labore et dolore magna aliqua. Ut enim ad minim veniam, quis nostrud exercitation ullamco laboris nisi ut aliquip exea commodo consequat.Duis aute irure dolor in reprehenderit in voluptate velit esse cillum irure dolor in reprehenderit in voluptate velit esse irure</p>
    </div>

    <div class="sign-off">Regards</div>
    <div class="signature" role="img" aria-label="Handwritten signature"></div>

    <div class="contact">
      <span class="contact-item">
        <svg viewBox="0 0 24 24" aria-hidden="true"><path fill="var(--crimson)" d="M6.6 10.8a15.5 15.5 0 0 0 6.6 6.6l2.2-2.2a1 1 0 0 1 1-.25 11.4 11.4 0 0 0 3.6.57 1 1 0 0 1 1 1V20a1 1 0 0 1-1 1A17 17 0 0 1 3 4a1 1 0 0 1 1-1h3.5a1 1 0 0 1 1 1c0 1.25.2 2.45.57 3.57a1 1 0 0 1-.25 1z"/></svg>
        832-361-9027
      </span>
      <span class="contact-item">
        <svg viewBox="0 0 24 24" aria-hidden="true"><path fill="var(--crimson)" d="M7 3h10v4H7zM4 8h16a2 2 0 0 1 2 2v6h-4v5H6v-5H2v-6a2 2 0 0 1 2-2zm4 8v3h8v-3z"/></svg>
        832-614-7359
      </span>
    </div>
    <div class="address">1475 Calloway Street, Suite 210, Houston, Texas 77041</div>
  </main>
</body>
</html>
```